Resposive web site in 4 languages + image gallery + logo design

We need a web page, which will work on all devices.
I have uploaded web page concept.
Company name: Praxelun
Industry/Entity Type
It Company
Logo Text
quality matters
Coding
Coded - Design and coding required
Number of Pages Required
1 page

```html
<!DOCTYPE html>
<html lang="en">
<head>
<meta charset="utf-8">
<title>Praxelun</title>
<link href="https://fonts.googleapis.com/css2?family=Roboto+Slab:wght@400;700&family=Raleway:wght@400;500;600&family=Arimo:wght@400;700&display=swap" rel="stylesheet">
<style>
:root{
  --orange:#f7a21b;
  --orange-dark:#e8900a;
  --ink:#333333;
  --text:#444444;
  --muted:#666666;
  --dark:#232323;
  --darker:#181818;
  --paper:#fbfbfb;
  --band:#ececec;
  --line:#dddddd;
  --white:#ffffff;
}
*{box-sizing:border-box;margin:0;padding:0}
html,body{width:1200px;height:2486px;overflow:hidden}
body{position:relative;background:var(--paper);font-family:"Raleway",sans-serif;color:var(--text)}
.abs{position:absolute}

/* header */
.hero-photo{position:absolute;left:0;top:0;width:1200px;height:600px;
  background:linear-gradient(180deg,#5d6a52 0%,#7d8275 30%,#8c8a86 55%,#6f6c69 80%,#5a5855 100%)}
.header-bar{position:absolute;left:0;top:0;width:1200px;height:80px}
.social-box{position:absolute;left:133px;top:12px;width:127px;height:27px;border:1px solid var(--orange);display:flex;align-items:center;justify-content:space-around;padding:0 8px}
.social-box span{width:12px;height:12px;background:var(--orange)}
.nav a{position:absolute;top:15px;font-family:"Raleway",sans-serif;font-size:14px;color:var(--white);text-decoration:none;letter-spacing:.3px}
.nav a.active{color:var(--orange);font-weight:600}
.brand{position:absolute;left:0;width:1200px;top:32px;text-align:center;font-family:"Roboto Slab",serif;font-weight:700;font-size:30px;color:var(--orange)}
.lang{position:absolute;left:983px;top:12px;width:84px;height:25px;border:1px solid #666;color:var(--white);font-size:11px;display:flex;align-items:center;gap:6px;padding-left:6px}
.lang i{width:20px;height:13px;background:#3b4f8a;display:block}

.welcome{position:absolute;left:133px;top:215px;width:380px;height:53px;background:linear-gradient(90deg,rgba(247,162,27,.85),rgba(247,162,27,0));padding:8px 10px;font-family:"Roboto Slab",serif;font-size:30px;color:var(--white)}
.welcome b{font-weight:700}
.hero-copy{position:absolute;left:133px;top:288px;width:330px;font-family:"Arimo",sans-serif;font-size:12px;line-height:16px;color:#111}
.btn{position:absolute;background:var(--orange);color:var(--white);font-size:12px;display:flex;align-items:center;justify-content:center;border-radius:2px;box-shadow:0 2px 0 var(--orange-dark)}
.estimate{position:absolute;left:186px;top:544px;font-family:"Arimo",sans-serif;font-weight:700;font-size:16px;color:var(--white)}
.quote-btn{position:absolute;left:938px;top:535px;width:123px;height:33px;background:#b97716;color:var(--white);font-family:"Arimo",sans-serif;font-size:14px;display:flex;align-items:center;justify-content:center}
.dots{position:absolute;left:574px;top:571px;display:flex;gap:5px}
.dots span{width:11px;height:11px;border-radius:50%;background:var(--white)}
.dots span:first-child{background:#c9c9c9}

/* services */
.section-title{position:absolute;left:0;width:1200px;text-align:center;font-family:"Roboto Slab",serif;font-weight:700;font-size:34px;color:var(--ink)}
.section-title em{font-style:normal;color:var(--orange)}
.title-rule{position:absolute;left:490px;width:220px;height:1px;background:var(--line)}
.service-band{position:absolute;left:0;top:1072px;width:1200px;height:366px;background:var(--band)}
.service-name{position:absolute;font-family:"Roboto Slab",serif;font-size:23px;color:var(--orange);letter-spacing:.5px}
.service-rule{position:absolute;height:1px;background:#d8d8d8}
.service-text{position:absolute;width:484px;font-size:12.5px;line-height:21.5px;color:var(--text)}
.links{position:absolute;left:0;width:1200px;display:flex;justify-content:center;gap:0;font-size:14px;color:var(--ink)}
.links li{list-style:none;padding:0 22px;border-left:1px solid #ccc;line-height:16px}
.links li:first-child{border-left:0;color:var(--orange)}
.links li::before{content:"›";margin-right:8px;font-weight:600}

.gallery{position:absolute;width:411px;height:257px;background:var(--white);border:1px solid #d5d5d5;padding:6px}
.gallery .photo{width:100%;height:100%}
.thumb{position:absolute;top:176px;width:63px;height:63px;border:2px solid #111}
.thumb.zoom{background:#222 !important;display:flex;align-items:center;justify-content:center}
.arrow{position:absolute;top:196px;width:14px;height:22px}

/* about */
.about-photo{position:absolute;left:0;top:1809px;width:1200px;height:375px;background:linear-gradient(90deg,#2a2620 0%,#3a3328 35%,#2f2c28 65%,#24221f 100%)}
.about-title{position:absolute;left:0;width:1200px;top:1880px;text-align:center;font-family:"Roboto Slab",serif;font-weight:700;font-size:34px;color:var(--white)}
.about-title em{font-style:normal;color:var(--orange)}
.about-brand{position:absolute;left:149px;top:2030px;font-family:"Roboto Slab",serif;font-weight:700;font-size:56px;color:var(--orange)}
.about-copy{position:absolute;left:524px;top:1968px;width:550px;font-family:"Arimo",sans-serif;font-size:12.5px;line-height:18px;color:var(--white)}
.about-copy p{margin-bottom:14px}
.motto{position:absolute;left:524px;top:2122px;font-family:"Arimo",sans-serif;font-size:16px;line-height:21px;color:var(--white)}
.motto b{color:var(--orange)}

/* footer */
.footer{position:absolute;left:0;top:2184px;width:1200px;height:260px;background:var(--dark)}
.foot-head{position:absolute;font-family:"Arimo",sans-serif;font-weight:700;font-size:13.5px;color:var(--orange)}
.foot-list{position:absolute;font-family:"Arimo",sans-serif;font-size:13px;color:#e6e6e6;list-style:none}
.foot-list li{height:25px}
.quick li::before{content:"›";margin-right:9px;color:#bbb}
.field{position:absolute;background:var(--white);border:1px solid #ccc;font-family:"Arimo",sans-serif;font-size:10.5px;color:#555;padding:5px 8px}
.submit{position:absolute;left:490px;top:2373px;width:178px;height:27px;background:var(--orange);color:var(--white);font-family:"Arimo",sans-serif;font-weight:700;font-size:14px;display:flex;align-items:center;justify-content:center}
.contact li{display:flex;align-items:center;gap:12px;height:27px}
.social li{display:flex;align-items:center;gap:9px;height:28.5px}
.social li span{width:18px;height:18px;background:var(--orange)}
.copyright{position:absolute;left:0;top:2444px;width:1200px;height:42px;background:var(--darker);color:#ddd;font-family:"Arimo",sans-serif;font-size:12px;display:flex;align-items:center;justify-content:center}
</style>
</head>
<body>

<!-- hero -->
<div class="hero-photo" role="img" aria-label="Stone garden staircase with retaining walls and an outdoor kitchen"></div>

<svg class="header-bar" viewBox="0 0 1200 80" aria-hidden="true">
  <path d="M0 0H1200V53H700C680 53 672 75 640 75H560C528 75 520 53 500 53H0Z" fill="rgba(28,28,28,.88)"/>
</svg>
<div class="social-box" aria-label="Social links"><span></span><span></span><span></span><span></span></div>
<nav class="nav">
  <a class="active" style="left:298px">HOME</a>
  <a style="left:398px">SERVICES</a>
  <a style="left:741px">ABOUT US</a>
  <a style="left:865px">CONTACT</a>
</nav>
<div class="brand">Praxelun</div>
<div class="lang"><i></i>English ▾</div>

<h1 class="welcome">Welcome to <b>Praxelun</b></h1>
<p class="hero-copy">At vero eos et accusamus et iusto odio dignissimos ducimus qui blanditiis praesentium voluptatum deleniti atque corrupti quos dolores et quas</p>
<div class="btn" style="left:133px;top:356px;width:98px;height:26px">LEARN MORE</div>

<svg class="abs" style="left:0;top:527px" width="1200" height="75" viewBox="0 0 1200 75" aria-hidden="true">
  <path d="M0 0H1200V56C900 56 760 58 640 70C610 73 590 73 560 70C440 58 300 56 0 56Z" fill="var(--orange)"/>
  <rect x="133" y="9" width="38" height="28" rx="5" fill="none" stroke="#fff" stroke-width="2"/>
  <rect x="158" y="17" width="13" height="11" rx="2" fill="none" stroke="#fff" stroke-width="2"/>
</svg>
<div class="estimate">Are you interested in an estimate?</div>
<div class="quote-btn">GET A QUOTE</div>
<div class="dots"><span></span><span></span><span></span></div>

<!-- services -->
<h2 class="section-title" style="top:640px">Our <em>Services</em></h2>
<div class="title-rule" style="top:704px"></div>

<!-- woodworks -->
<div class="gallery" style="left:133px;top:739px">
  <div class="photo" role="img" aria-label="Timber house frame under construction" style="background:linear-gradient(180deg,#a9c4de 0%,#d8c2a0 45%,#b38c5e 100%)"></div>
  <div class="thumb zoom" style="left:50px"><svg width="16" height="16"><circle cx="7" cy="7" r="5" fill="none" stroke="#fff" stroke-width="2"/><path d="M11 11L15 15" stroke="#fff" stroke-width="2"/></svg></div>
  <div class="thumb" style="left:133px;background:#c9b8a0"></div>
  <div class="thumb" style="left:215px;background:#7a3e1e"></div>
  <div class="thumb" style="left:298px;background:#a57849"></div>
  <svg class="arrow" style="left:28px"><path d="M11 2L3 11L11 20" stroke="#fff" stroke-width="3" fill="none"/></svg>
  <svg class="arrow" style="left:370px"><path d="M3 2L11 11L3 20" stroke="#fff" stroke-width="3" fill="none"/></svg>
</div>
<h3 class="service-name" style="left:582px;top:733px">WOODWORKS</h3>
<div class="service-rule" style="left:582px;top:775px;width:484px"></div>
<p class="service-text" style="left:582px;top:792px">Timber is, in essence, a natural and warm material. Wood is also relatively durable and easy to workwith, which has made it a favourite of builders throughout history. Our goal is to offer GALLERY (sliders) suitable products and quality furniture with installation and after - When cliked opens sales service to all of our clients. In order to achieve this, we're this category gallery ready to help our clients in all stages of construction from design to production and maintenance.</p>
<div class="btn" style="left:582px;top:963px;width:85px;height:26px">Read More</div>
<ul class="links" style="top:1027px"><li>Furniture</li><li>Windows</li><li>Doors</li><li>Staircases</li><li>Woodcarving</li><li>Graining</li></ul>

<!-- stoneworks -->
<div class="service-band"></div>
<h3 class="service-name" style="left:133px;top:1099px">STONEWORKS</h3>
<div class="service-rule" style="left:133px;top:1141px;width:484px"></div>
<p class="service-text" style="left:133px;top:1160px">The natural stone found in the ground has been used in construction for centuries because of its durability. A structure built by a skilled craftsman from natural stone is unique, genuine and durable, and perfect for our bracing climate.Our experienced craftsmen are ready to help you in all stages of construction from planning to completion. Lorem ipsum dolor sit amet, consectetuer adipiscing elit, sed diam nonummy. sit amet, consectetuer adipiscing elit.</p>
<div class="btn" style="left:133px;top:1334px;width:85px;height:26px">Read More</div>
<div class="gallery" style="left:655px;top:1105px">
  <div class="photo" role="img" aria-label="Kitchen interior with a stacked stone feature wall" style="background:linear-gradient(90deg,#c9b49a 0%,#a98a6a 50%,#5a3a25 80%,#3d2a1e 100%)"></div>
  <div class="thumb zoom" style="left:50px"><svg width="16" height="16"><circle cx="7" cy="7" r="5" fill="none" stroke="#fff" stroke-width="2"/><path d="M11 11L15 15" stroke="#fff" stroke-width="2"/></svg></div>
  <div class="thumb" style="left:133px;background:#b9b3a6"></div>
  <div class="thumb" style="left:215px;background:#8a6747"></div>
  <div class="thumb" style="left:298px;background:#6e4a30"></div>
  <svg class="arrow" style="left:28px"><path d="M11 2L3 11L11 20" stroke="#fff" stroke-width="3" fill="none"/></svg>
  <svg class="arrow" style="left:370px"><path d="M3 2L11 11L3 20" stroke="#fff" stroke-width="3" fill="none"/></svg>
</div>
<ul class="links" style="top:1395px"><li>Walls</li><li>Terraces</li><li>Paths</li><li>Outdoor kitchens</li><li>Fireplaces</li><li>Smokeries</li><li>Fences</li></ul>

<!-- restoration -->
<div class="gallery" style="left:133px;top:1471px">
  <div class="photo" role="img" aria-label="Historic building facade covered in scaffolding" style="background:linear-gradient(180deg,#b9cde3 0%,#d8d0c2 35%,#a89a86 75%,#8b7e6c 100%)"></div>
  <div class="thumb zoom" style="left:50px"><svg width="16" height="16"><circle cx="7" cy="7" r="5" fill="none" stroke="#fff" stroke-width="2"/><path d="M11 11L15 15" stroke="#fff" stroke-width="2"/></svg></div>
  <div class="thumb" style="left:133px;background:#a89f90"></div>
  <div class="thumb" style="left:215px;background:#8f877a"></div>
  <div class="thumb" style="left:298px;background:#c4bcae"></div>
  <svg class="arrow" style="left:28px"><path d="M11 2L3 11L11 20" stroke="#fff" stroke-width="3" fill="none"/></svg>
  <svg class="arrow" style="left:370px"><path d="M3 2L11 11L3 20" stroke="#fff" stroke-width="3" fill="none"/></svg>
</div>
<h3 class="service-name" style="left:582px;top:1466px">RESTORATION</h3>
<div class="service-rule" style="left:582px;top:1508px;width:484px"></div>
<p class="service-text" style="left:582px;top:1527px">It's good to see that fixing old things has become popular again in recent years and people are trying to find ways to preserve valuable old windows and pieces of furniture before deciding to replace them. It is possible to give a new life to almost any wooden door, window, piece of furniture or staircase. The extensive experience of our craftsmen will help you achieve the desired result. Lorem ipsum dolor sit amet, consectetuer adipiscing elit, sed diam nonummy. sit amet, consectetuer adipiscing elit.</p>
<div class="btn" style="left:582px;top:1697px;width:85px;height:26px">Read More</div>
<ul class="links" style="top:1761px"><li>Furniture</li><li>Windows</li><li>Doors</li><li>Staircases</li><li>Floors</li><li>Special Projects</li></ul>

<!-- about -->
<div class="about-photo" role="img" aria-label="Team of builders in hard hats"></div>
<svg class="abs" style="left:0;top:1800px" width="1200" height="40" viewBox="0 0 1200 40" aria-hidden="true">
  <path d="M0 0H1200V9C900 9 760 11 640 23C610 26 590 26 560 23C440 11 300 9 0 9Z" fill="var(--paper)"/>
  <path d="M0 9C300 9 440 11 560 23C590 26 610 26 640 23C760 11 900 9 1200 9" stroke="var(--orange)" stroke-width="3" fill="none"/>
</svg>
<h2 class="about-title">About <em>us</em></h2>
<div class="title-rule" style="top:1942px;background:#555"></div>
<div class="about-brand">Praxelun</div>
<div class="about-copy">
  <p>Praxelun is a company whose business operations include making wooden products restoration and building structures from natural stone.</p>
  <p>All of our products are made by craftsmen and specialists who have extensive experience and knowledge in their fields.</p>
  <p>The products we offer are always handmade and we take the requests and ideas of the specific client into account We always strive to achieve the best possible quality.</p>
</div>
<div class="motto">Quality matters,<br><b>Praxelun</b></div>

<!-- footer -->
<div class="footer"></div>
<svg class="abs" style="left:0;top:2176px" width="1200" height="30" viewBox="0 0 1200 30" aria-hidden="true">
  <path d="M0 8C300 8 440 10 560 20C590 23 610 23 640 20C760 10 900 8 1200 8V30H0Z" fill="#3a3a3a"/>
  <path d="M0 12C300 12 440 14 560 24C590 27 610 27 640 24C760 14 900 12 1200 12V30H0Z" fill="var(--dark)"/>
</svg>

<div class="foot-head" style="left:136px;top:2246px">Quick Links</div>
<ul class="foot-list quick" style="left:136px;top:2284px"><li>Home</li><li>Services</li><li>About</li><li>Contact Us</li></ul>

<div class="foot-head" style="left:306px;top:2245px;width:362px;text-align:center;line-height:22px">PLEASE FILL IN THE FOLLOWING FIELDS IF YOU WOULD LIKE A PRICE QUOTE</div>
<div class="field" style="left:306px;top:2301px;width:178px;height:28px">Name</div>
<div class="field" style="left:306px;top:2337px;width:178px;height:28px">Telephone</div>
<div class="field" style="left:306px;top:2372px;width:178px;height:28px">Email</div>
<div class="field" style="left:490px;top:2301px;width:178px;height:65px">Message</div>
<div class="submit">Submit</div>

<div class="foot-head" style="left:742px;top:2243px">Contact Information</div>
<div class="abs" style="left:742px;top:2272px;font-family:'Arimo',sans-serif;font-size:12.5px;line-height:19px;color:#e6e6e6;width:170px"><b>Praxelun</b> at vero eos et accusamus-123456</div>
<ul class="foot-list contact" style="left:742px;top:2320px">
  <li><svg width="12" height="12"><path d="M2 1L5 1L6 4L4 5Q6 8 8 9L9 7L12 8L12 11Q5 12 1 3Z" fill="var(--orange)"/></svg>123 456 789</li>
  <li><svg width="12" height="12"><rect x="1" y="4" width="10" height="7" fill="var(--orange)"/><rect x="3" y="1" width="6" height="3" fill="none" stroke="var(--orange)"/></svg>123 456 789</li>
  <li><svg width="12" height="12"><rect x="1" y="3" width="10" height="7" fill="var(--orange)"/><path d="M1 3L6 7L11 3" stroke="#232323" fill="none"/></svg>info@praxelun.com</li>
</ul>

<div class="foot-head" style="left:981px;top:2246px">Follow us</div>
<ul class="foot-list social" style="left:981px;top:2278px">
  <li><span></span>Friendwall</li>
  <li><span></span>Chirpline</li>
  <li><span></span>Circlecast</li>
  <li><span></span>Worklink</li>
</ul>

<div class="copyright">Copyright © 2016 Praxelun. All Right Reserved.</div>
</body>
</html>
```